K7 Electrical Services Ltd Web design

I require a web site for my new electrical contracting company. We are customer service orientated. Offering high value electrical installations, design and maintenance. Focused on custom residential and commercial upgrading. Lighting design and application are paramount in our company's services. Industry leading product use and integration are always on the forefront with our customer client services. As well as energy efficiency.

Target Market(s)

Homebuilders, General Contractors, Property management companies, clients, individuals,

Industry/Entity Type

Electric Company

Coding

Coded - Design and coding required

Number of Pages Required

3 page

Requirements
Must have
• Classic, modern, edgy but not trendy . Appeals to the masse.
• 3 page
• home page
• about page
• gallery page
• ability to contact from the webiste
Nice to have
• open to all types of designs that are relative to the construction industry.
• Black, Grey, metallic ice blue and deep purple colours from the logo.
Should not have
• anything cheesy with cartoon light bulb images.

```html
<!DOCTYPE html>
<html lang="en">
<head>
<meta charset="utf-8">
<title>K7 Electrical Services Ltd</title>
<link href="https://fonts.googleapis.com/css2?family=Maven+Pro:wght@400;500;600;700&family=Arimo:wght@400;700&display=swap" rel="stylesheet">
<style>
:root{
  --purple:#5b2a8c;
  --purple-dark:#4a1f78;
  --purple-light:#8a63b8;
  --grey:#7c7c7e;
  --grey-text:#9a9a9a;
  --light:#f2f2f2;
  --ink:#222;
  --footer-dark:#3d3d3d;
  --white:#fff;
}
*{box-sizing:border-box;margin:0;padding:0}
html,body{width:1200px;height:3237px;overflow:hidden}
body{font-family:"Arimo",Arial,sans-serif;color:var(--ink);background:var(--white);position:relative}
.heading-font{font-family:"Maven Pro",Arial,sans-serif}

/* header */
.site-header{height:85px;position:relative}
.brand{position:absolute;left:142px;top:22px;font-family:"Maven Pro",sans-serif;font-weight:700;font-size:22px;color:var(--purple);display:flex;align-items:center;gap:10px}
.brand-square{width:18px;height:18px;background:var(--purple)}
.header-cta{position:absolute;right:142px;top:16px;font-family:"Maven Pro",sans-serif;font-weight:700;font-size:15px;color:var(--purple)}
.main-nav{position:absolute;right:142px;top:52px;display:flex;gap:44px;font-family:"Maven Pro",sans-serif;font-weight:500;font-size:14px;color:#333}
.main-nav .active{color:var(--purple)}

/* hero */
.hero{height:513px;position:relative;background:linear-gradient(180deg,#2d4a5a 0%,#5d7f8c 35%,#3a3a34 62%,#6b4a22 78%,#1e1a16 100%)}
.hero-arrow{position:absolute;top:242px;width:36px;height:30px;background:#333;display:flex;align-items:center;justify-content:center}
.hero-arrow.prev{left:2px}.hero-arrow.next{right:2px}
.hero-caption{position:absolute;left:0;right:0;top:428px;text-align:center;font-family:"Maven Pro",sans-serif;font-size:31px;color:var(--white);text-shadow:0 2px 4px rgba(0,0,0,.6)}

/* service split */
.service-split{height:207px;display:flex;position:relative}
.service-panel{flex:1;padding:14px 0 0;color:var(--white)}
.service-panel.residential{background:var(--purple);padding-left:148px}
.service-panel.commercial{background:var(--grey);padding-left:138px}
.service-title{display:flex;align-items:center;gap:14px;font-family:"Maven Pro",sans-serif;font-weight:700;font-size:25px;margin-bottom:8px}
.service-rule{width:310px;height:1px;background:rgba(255,255,255,.45);margin-bottom:10px}
.service-text{width:310px;font-size:10.5px;line-height:17px}
.split-badge{position:absolute;left:508px;top:8px;width:184px;height:184px;border-radius:50%;background:var(--white);border:8px solid #c9c0d4;display:flex;align-items:center;justify-content:center;text-align:center;font-family:"Maven Pro",sans-serif;font-weight:700;font-size:18px;line-height:22px;color:var(--purple);padding:18px}

/* intro */
.intro{height:460px;position:relative;text-align:center}
.intro-brand{padding-top:62px;font-family:"Maven Pro",sans-serif;font-weight:700;font-size:28px;color:var(--purple)}
.intro-text{margin:26px auto 0;width:920px;font-size:14px;line-height:24px;color:#333}
.feature-row{position:absolute;top:261px;left:142px;display:flex;gap:35px}
.feature-card{width:283px;height:147px;border:1px solid #e6e6e6;position:relative;padding-top:68px;font-family:"Maven Pro",sans-serif;font-size:21px;line-height:25px;color:#555}
.feature-icon{position:absolute;left:50%;top:-68px;margin-left:-46px;width:92px;height:104px}

/* section titles */
.section-title{font-family:"Maven Pro",sans-serif;font-weight:700;font-size:34px;color:var(--purple);text-align:center}
.section-title .muted{color:var(--grey-text)}
.title-rule{width:112px;height:4px;margin:10px auto 0;background:linear-gradient(90deg,var(--purple) 50%,var(--grey-text) 50%)}

/* about */
.about{height:385px;background:var(--light);padding-top:48px;text-align:center}
.about .section-title{display:flex;justify-content:center;align-items:baseline;gap:14px}
.about-brand{font-size:26px;color:var(--purple)}
.about-text{width:1000px;margin:20px auto 0;font-size:10.5px;line-height:22px;color:#333}
.about-text+.about-text{margin-top:8px}
.btn{display:inline-block;background:var(--purple);color:var(--white);font-family:"Maven Pro",sans-serif;font-weight:700;border-radius:8px}
.about .btn{margin-top:20px;font-size:21px;padding:9px 26px}

/* gallery */
.gallery{height:670px;position:relative;padding-top:48px}
.gallery-grid{position:absolute;left:142px;top:130px;width:916px;height:490px}
.tile{position:absolute}
.tile-feature{left:0;top:0;width:336px;height:288px;background:#4a4a4c;color:var(--white);text-align:center;padding:60px 22px 0}
.tile-feature h3{font-family:"Maven Pro",sans-serif;font-size:21px;line-height:24px;font-weight:500;margin-bottom:4px}
.tile-feature p{font-size:10.5px;line-height:16px}
.t2{left:346px;top:0;width:327px;height:140px;background:linear-gradient(135deg,#d9d3cf,#b43a2a 55%,#e0ddd8)}
.t3{left:346px;top:148px;width:159px;height:140px;background:linear-gradient(180deg,#5a3a22,#c08650 60%,#3e2a1e)}
.t4{left:513px;top:148px;width:160px;height:140px;background:linear-gradient(135deg,#c9c6c0,#c2483a 50%,#6d7a8a)}
.t5{left:681px;top:0;width:235px;height:288px;background:linear-gradient(180deg,#efe6d6,#8aa4c4 55%,#c9a77a)}
.t6{left:0;top:298px;width:505px;height:192px;background:linear-gradient(120deg,#e7e4df,#9aa1a8 45%,#c88a3a 75%,#e9e6e0)}
.t7{left:513px;top:298px;width:403px;height:192px;background:linear-gradient(135deg,#3a2418,#b06a34 50%,#e2c69c)}

/* why choose */
.why{height:232px;background:var(--light);padding-top:48px;text-align:center}
.why-text{margin-top:30px;font-family:"Maven Pro",sans-serif;font-weight:500;font-size:15.5px;line-height:24px;color:#222}
.why-link{color:var(--purple);font-weight:700}

/* contact */
.contact{height:503px;position:relative;padding-top:52px}
.contact-form{position:absolute;left:170px;top:152px;width:381px}
.field{width:381px;height:44px;border:2px solid #c8b6de;border-radius:10px;margin-bottom:10px;padding:10px 14px;font-size:16px;color:#333}
.field.message{height:84px}
.req{color:#c0392b}
.contact-form .btn{font-size:20px;padding:9px 28px;border-radius:6px;margin-top:-2px}
.contact-info{position:absolute;left:616px;top:152px;width:442px}
.contact-info h3{font-family:"Maven Pro",sans-serif;font-weight:700;font-size:25px;color:var(--purple);padding-bottom:6px;border-bottom:1px solid #ccc;margin-bottom:12px}
.contact-info p{font-family:"Maven Pro",sans-serif;font-size:16px;line-height:30px;color:#333}
.map{margin-top:12px;width:440px;height:136px;background:linear-gradient(135deg,#e9e6df,#dfe9dc 55%,#d8e4ee);border:1px solid #ddd}

/* footer */
.site-footer{height:138px;background:var(--purple);text-align:center;padding-top:26px;color:var(--white)}
.footer-nav{display:flex;justify-content:center;gap:24px;font-size:11px}
.footer-brand{margin-top:22px;font-family:"Maven Pro",sans-serif;font-weight:700;font-size:24px}
.copyright{height:44px;background:var(--footer-dark);color:#ddd;font-size:11px;text-align:center;line-height:44px}
</style>
</head>
<body>

<header class="site-header">
  <div class="brand"><span class="brand-square"></span>K7 Electrical Services Ltd</div>
  <div class="header-cta">SCHEDULE YOUR SERVICE TODAY</div>
  <nav class="main-nav"><span class="active">HOME</span><span>ABOUT US</span><span>GALLERY</span><span>CONTACT US</span></nav>
</header>

<section class="hero" role="img" aria-label="Photograph of a lakeside deck lit by warm outdoor lighting at dusk">
  <div class="hero-arrow prev"><svg width="12" height="14" viewBox="0 0 12 14"><path d="M9 1 3 7l6 6" fill="none" stroke="#fff" stroke-width="2.5"/></svg></div>
  <div class="hero-arrow next"><svg width="12" height="14" viewBox="0 0 12 14"><path d="M3 1l6 6-6 6" fill="none" stroke="#fff" stroke-width="2.5"/></svg></div>
  <p class="hero-caption">Offering High Value Electrical Installations, Design &amp; Maintenance</p>
</section>

<section class="service-split">
  <div class="service-panel residential">
    <h2 class="service-title">
      <svg width="44" height="40" viewBox="0 0 44 40" fill="none" stroke="#fff" stroke-width="2"><path d="M3 19 22 4l19 15"/><path d="M8 16v21h28V16"/><rect x="18" y="25" width="8" height="12"/><rect x="12" y="19" width="6" height="5"/><rect x="26" y="19" width="6" height="5"/></svg>
      Residential</h2>
    <div class="service-rule"></div>
    <p class="service-text">Lorem ipsum dolor sit amet, consectetuer adipiscing elit, sed diam nonummy nibh euismod tincidunt ut laoreet dolore magna aliquam erat volutpat. Ut wisi enim ad minim veniam, quis nostrud exerci tation ullamcorper suscipit lobortis nisl ut aliquip ex ea commodo consequat.</p>
  </div>
  <div class="service-panel commercial">
    <h2 class="service-title">
      <svg width="44" height="40" viewBox="0 0 44 40" fill="none" stroke="#fff" stroke-width="2"><rect x="6" y="10" width="14" height="28"/><rect x="20" y="3" width="18" height="35"/><path d="M24 9h4M30 9h4M24 15h4M30 15h4M24 21h4M30 21h4M24 27h4M30 27h4M10 16h6M10 22h6M10 28h6M2 38h40"/></svg>
      Commerical</h2>
    <div class="service-rule"></div>
    <p class="service-text">Lorem ipsum dolor sit amet, consectetuer adipiscing elit, sed diam nonummy nibh euismod tincidunt ut laoreet dolore magna aliquam erat volutpat. Ut wisi enim ad minim veniam, quis nostrud exerci tation ullamcorper suscipit lobortis nisl ut aliquip ex ea commodo consequat.</p>
  </div>
  <div class="split-badge">K7 Electrical Services Ltd</div>
</section>

<section class="intro">
  <div class="intro-brand">K7 Electrical Services Ltd</div>
  <p class="intro-text">We are customer service orientated. Offering high value &nbsp;text of the printing and typesetting industry. Lorem Ipsum has been the industry's standard dummy text ever since the 1500s.</p>
  <div class="feature-row">
    <div class="feature-card">
      <svg class="feature-icon" viewBox="0 0 92 104"><path d="M46 2 88 26v52L46 102 4 78V26z" fill="var(--purple)"/><g fill="#fff"><rect x="37" y="28" width="4" height="12"/><rect x="51" y="28" width="4" height="12"/><path d="M32 40h28v10a14 14 0 0 1-28 0z"/><rect x="43" y="62" width="6" height="14"/></g></svg>
      Electrical<br>Installations
    </div>
    <div class="feature-card">
      <svg class="feature-icon" viewBox="0 0 92 104"><path d="M46 2 88 26v52L46 102 4 78V26z" fill="var(--purple)"/><g stroke="#fff" stroke-width="6" stroke-linecap="round" fill="none"><path d="M30 34l32 36"/><path d="M62 34 34 66"/></g><circle cx="62" cy="34" r="8" fill="#fff"/><circle cx="30" cy="34" r="6" fill="#fff"/></svg>
      Design And<br>Maintenance
    </div>
    <div class="feature-card">
      <svg class="feature-icon" viewBox="0 0 92 104"><path d="M46 2 88 26v52L46 102 4 78V26z" fill="var(--purple)"/><circle cx="46" cy="52" r="13" fill="none" stroke="#fff" stroke-width="4"/><rect x="43" y="45" width="6" height="14" fill="#fff"/><g stroke="#fff" stroke-width="3" stroke-linecap="round"><path d="M46 28v6M46 70v6M22 52h6M64 52h6M29 35l4 4M59 65l4 4M63 35l-4 4M33 65l-4 4"/></g></svg>
      Lighting Design And<br>Application
    </div>
  </div>
</section>

<section class="about">
  <h2 class="section-title">ABOUT <span class="about-brand">K7 Electrical Services Ltd</span></h2>
  <div class="title-rule"></div>
  <p class="about-text">Lorem ipsum dolor sit amet, consectetuer adipiscing elit, sed diam nonummy nibh euismod tincidunt ut laoreet dolore magna aliquam erat volutpat. Ut wisi enim ad minim veniam, quis nostrud exerci tation ullamcorper suscipit lobortis nisl ut aliquip ex ea commodo consequat.</p>
  <p class="about-text">Lorem ipsum dolor sit amet, consectetuer adipiscing elit, sed diam nonummy nibh euismod tincidunt ut laoreet dolore magna aliquam erat volutpat. Ut wisi enim ad minim veniam, quis nostrud exerci tation ullamcorper suscipit lobortis nisl ut aliquip ex ea commodo consequat. Duis autem vel eum iriure dolor in hendrerit in vulputate velit esse molestie consequat, vel illum dolore eu feugiat nulla facilisis at vero eros et accumsan et iusto odio dignissim qui blandit praesent luptatum zzril delenit augue duis dolore te feugait nulla facilisi. Duis autem vel eum iriure dolor in hendrerit in vulputate velit esse molestie consequat, vel illum dolore eu feugiat nulla facilisis at vero eros et accumsan et iusto odio dignissim qui blandit praesent luptatum zzril delenit augue duis dolore te feugait nulla facilisi.</p>
  <span class="btn">Call Us Today</span>
</section>

<section class="gallery">
  <h2 class="section-title">WORK <span class="muted">GALLERY</span></h2>
  <div class="title-rule"></div>
  <div class="gallery-grid">
    <div class="tile tile-feature">
      <h3>Electrical<br>Installations</h3>
      <p>Lorem ipsum dolor sit amet, consectetuer adipiscing elit, sed diam nonummy nibh euismod tincidunt ut laoreet dolore magna aliquam erat volutpat. Ut wisi enim ad minim veniam, quis nostrud exerci tation ullamcorper suscipit lobortis nisl ut aliquip ex ea commodo consequat.</p>
    </div>
    <div class="tile t2" role="img" aria-label="Photo of hands stripping coloured electrical wires"></div>
    <div class="tile t3" role="img" aria-label="Photo of a staircase with warm step lighting"></div>
    <div class="tile t4" role="img" aria-label="Photo of wiring inside a breaker panel"></div>
    <div class="tile t5" role="img" aria-label="Photo of an electrician fitting a ceiling light"></div>
    <div class="tile t6" role="img" aria-label="Photo of a multimeter testing a circuit breaker panel"></div>
    <div class="tile t7" role="img" aria-label="Photo of a modern interior with accent lighting"></div>
  </div>
</section>

<section class="why">
  <h2 class="section-title">WHY CHOOSE <span class="muted">US</span></h2>
  <div class="title-rule"></div>
  <p class="why-text">Lighting design and application are paramount in our company's services.<br>Industry leading product use &amp; integration are always on the forefront with our customer client services.<br><span class="why-link">SCHEDULE YOUR SERVICE TODAY</span></p>
</section>

<section class="contact">
  <h2 class="section-title">GET IN <span class="muted">TOUCH</span></h2>
  <div class="title-rule"></div>
  <form class="contact-form">
    <div class="field">Name<span class="req">*</span></div>
    <div class="field">Phone</div>
    <div class="field">Email<span class="req">*</span></div>
    <div class="field message">Message<span class="req">*</span></div>
    <span class="btn">SUBMIT</span>
  </form>
  <div class="contact-info">
    <h3>SCHEDULE YOUR SERVICE TODAY</h3>
    <p>CALL US : 555-014-2290</p>
    <p>OUR OFFICE :Street Name, City Name State Zipcode</p>
    <div class="map" role="img" aria-label="Street map showing the office location"></div>
  </div>
</section>

<footer class="site-footer">
  <nav class="footer-nav"><span>HOME</span><span>ABOUT US</span><span>GALLERY</span><span>CONTACT US</span></nav>
  <div class="footer-brand">K7 Electrical Services Ltd</div>
</footer>
<div class="copyright">Copyright &copy;2018 K7ElectricalServices.com. All Rights Reserved.</div>

</body>
</html>
```